U.S. Popcorn company needs business cards

We are a popcorn company that manufactures popcorn and sells it to grocery stores worldwide. Our theme is "Americana" and our logo is U.S. route 66 which is the most famous highway in the U.S.

We would like the design to be simple and to use both sides. On the back side we would like to see just the logo and website. The front would be normal details

Target Market(s)

Wholesalers, grocers and distributors

Industry/Entity Type

Manufacture

Contact Information for Business Card

Business name: Prairie Lantern Popcorn
Phone: +1 555 308 4726
Email: Dale@prairielanternpopcorn.com
website: www.prairielanternpopcorn.com
Tag Line: "Fresh from the field"
Name: Dale Whitcombe
Title: Founder/President

Requirements
Must have
• Either this design should be fun or clean and simple. I will let you show me your thougths.
Nice to have
• Anything that ties in the real Hwy Route 66.
• Colors might need to be red, white and blue incorporated.
Should not have
• Not be too busy.

```html
<!DOCTYPE html>
<html lang="en">
<head>
<meta charset="utf-8">
<title>Prairie Lantern Popcorn – Business Cards</title>
<link rel="stylesheet" href="https://fonts.googleapis.com/css2?family=Mulish:wght@400;700;800&display=swap">
<style>
  :root {
    --navy: #12306a;
    --red: #d9252a;
    --white: #ffffff;
    --card-white: #f7f7f8;
    --backdrop: #e6e6e6;
  }
  * { margin: 0; padding: 0; box-sizing: border-box; }
  html, body { width: 1200px; height: 576px; overflow: hidden; }
  body {
    background: var(--backdrop);
    font-family: "Mulish", Arial, sans-serif;
    position: relative;
  }
  .card {
    position: absolute;
    top: 139px;
    width: 485px;
    height: 293px;
    border-radius: 8px;
    background: var(--card-white);
    overflow: hidden;
  }
  .card-back { left: 82px; }
  .card-front { left: 602px; }

  .brand-name {
    color: var(--navy);
    font-weight: 800;
    text-align: center;
    line-height: 1.08;
    display: flex;
    flex-direction: column;
    align-items: center;
    gap: 8px;
  }
  .brand-dot {
    width: 18px; height: 18px;
    border-radius: 50%;
    background: var(--red);
  }
  .card-back .brand-name {
    position: absolute;
    left: 0; right: 0; top: 88px;
    font-size: 30px;
  }
  .back-website {
    position: absolute;
    left: 0; right: 0; top: 256px;
    display: flex;
    justify-content: center;
    align-items: center;
    gap: 10px;
    font-size: 12px;
    font-weight: 700;
    color: var(--navy);
  }
  .back-website .rule {
    width: 46px; height: 2px;
    background: var(--navy);
    border-radius: 1px;
  }
  .back-website .domain { color: var(--red); }

  .front-art { position: absolute; inset: 0; width: 100%; height: 100%; }
  .person {
    position: absolute; left: 21px; top: 37px;
    color: var(--white);
  }
  .person-name { font-size: 22px; font-weight: 700; line-height: 1.15; }
  .person-title { font-size: 12px; margin-top: 2px; }
  .contacts {
    position: absolute; left: 21px; top: 180px;
    list-style: none;
    color: var(--white);
    font-size: 13px;
  }
  .contacts li {
    display: flex; align-items: center; gap: 9px;
    height: 18px;
  }
  .contacts svg { width: 13px; height: 13px; flex: none; }
  .tagline {
    position: absolute; left: 21px; top: 248px;
    color: var(--white);
    font-size: 14px;
    line-height: 18px;
  }
  .tagline strong { font-weight: 800; }
  .card-front .brand-name {
    position: absolute;
    left: 300px; width: 176px; top: 104px;
    font-size: 22px;
  }
</style>
</head>
<body>

<section class="card card-back" aria-label="Card back">
  <div class="brand-name">
    <span class="brand-dot"></span>
    <span>Prairie Lantern<br>Popcorn</span>
  </div>
  <div class="back-website">
    <span class="rule"></span>
    <span>www.<span class="domain">prairielanternpopcorn</span>.com</span>
    <span class="rule"></span>
  </div>
</section>

<section class="card card-front" aria-label="Card front">
  <svg class="front-art" viewBox="0 0 485 293" preserveAspectRatio="none">
    <path d="M0 0 H278 C252 70 246 190 298 293 H0 Z" fill="var(--navy)"/>
    <path d="M326 0 C290 40 266 110 268 168 C270 222 286 252 300 268 C284 240 276 205 276 165 C276 105 292 45 316 0 Z" fill="var(--red)"/>
    <path d="M0 242 H276 C279 253 283 263 288 273 H0 Z" fill="var(--red)"/>
  </svg>

  <div class="person">
    <div class="person-name">Dale Whitcombe</div>
    <div class="person-title">Founder/President</div>
  </div>

  <ul class="contacts">
    <li>
      <svg viewBox="0 0 16 16"><path fill="#fff" d="M2 6 C2 3 14 3 14 6 L12 7 L11 5.5 C9 5 7 5 5 5.5 L4 7 Z M4 8 H12 L13 13 H3 Z"/></svg>
      +1 555 308 4726
    </li>
    <li>
      <svg viewBox="0 0 16 16"><rect x="1.5" y="3.5" width="13" height="9" fill="none" stroke="#fff" stroke-width="1.5"/><path d="M1.5 3.5 L8 9 L14.5 3.5" fill="none" stroke="#fff" stroke-width="1.5"/></svg>
      Dale@prairielanternpopcorn.com
    </li>
    <li>
      <svg viewBox="0 0 16 16"><circle cx="8" cy="8" r="6.3" fill="none" stroke="#fff" stroke-width="1.3"/><ellipse cx="8" cy="8" rx="2.6" ry="6.3" fill="none" stroke="#fff" stroke-width="1.1"/><path d="M1.7 8 H14.3" stroke="#fff" stroke-width="1.1"/></svg>
      prairielanternpopcorn.com
    </li>
  </ul>

  <p class="tagline">"<strong>Fresh</strong> from the field"</p>

  <div class="brand-name">
    <span class="brand-dot"></span>
    <span>Prairie Lantern<br>Popcorn</span>
  </div>
</section>

</body>
</html>
```